business card deign

Logo needs the following on it.
1. attached logo
2. Tagline - "From chilled drinks to lively nights...we bring it all!"
3. Name- Dalton Pikes, Founder and CPO
4. Address - 412 E. Carver Avenue, Ste 2207, Harlow, NC. 33917
5. Phone - 555.318.4726

```html
<!DOCTYPE html>
<html lang="en">
<head>
<meta charset="UTF-8">
<title>Hopply Business Card</title>
<link href="https://fonts.googleapis.com/css2?family=Montserrat:wght@400;500;700&display=swap" rel="stylesheet">
<style>
  :root {
    --ink: #141414;
    --paper: #ffffff;
    --backdrop: #d9d9d9;
    --rule: #2a2a2a;
  }
  * { margin: 0; padding: 0; box-sizing: border-box; }
  html, body {
    width: 1200px; height: 900px; overflow: hidden;
    background: var(--backdrop);
    font-family: "Montserrat", sans-serif;
    color: var(--ink);
  }
  .card {
    position: absolute;
    left: 250px;
    width: 700px; height: 400px;
    border-radius: 34px;
    overflow: hidden;
  }
  .card-front { top: 35px; background: var(--ink); }
  .card-back { top: 465px; background: var(--paper); }

  .brand {
    position: absolute;
    display: flex; align-items: center; gap: 14px;
    font-weight: 700;
    letter-spacing: 10px;
  }
  .brand-dot { width: 18px; height: 18px; border-radius: 50%; }
  .card-front .brand { left: 50%; top: 50%; transform: translate(-50%, -50%); color: var(--paper); font-size: 40px; }
  .card-front .brand-dot { background: var(--paper); }
  .card-back .brand { left: 62px; top: 150px; color: var(--ink); font-size: 34px; }
  .card-back .brand-dot { background: var(--ink); }

  .divider {
    position: absolute; left: 350px; top: 60px;
    width: 1.5px; height: 200px; background: var(--rule);
  }
  .contact { position: absolute; left: 378px; top: 62px; }
  .contact-name { font-size: 22px; font-weight: 700; }
  .contact-role { font-size: 13px; margin-top: 2px; }
  .contact-address { font-size: 13px; line-height: 1.35; margin-top: 16px; }
  .contact-list { list-style: none; margin-top: 12px; font-size: 14px; }
  .contact-list li { display: flex; align-items: center; gap: 10px; margin-bottom: 8px; }
  .contact-list svg { width: 13px; height: 13px; fill: var(--ink); }

  .bands { position: absolute; inset: 0; }
  .tagline {
    position: absolute; left: 38px; top: 340px;
    height: 35px; line-height: 35px;
    color: var(--paper); font-size: 15px; letter-spacing: 0.3px;
  }
</style>
</head>
<body>
  <section class="card card-front">
    <div class="brand"><span class="brand-dot"></span>HOPPLY</div>
  </section>

  <section class="card card-back">
    <svg class="bands" viewBox="0 0 700 400" aria-hidden="true">
      <polygon points="460,275 700,275 700,305 540,305" fill="#141414"/>
      <polygon points="0,340 700,340 700,375 0,375" fill="#141414"/>
    </svg>

    <div class="brand"><span class="brand-dot"></span>HOPPLY</div>
    <div class="divider"></div>

    <div class="contact">
      <h1 class="contact-name">Dalton Pikes</h1>
      <p class="contact-role">Founder and CPO</p>
      <p class="contact-address">412 E. Carver Avenue, Ste 2207,<br>Harlow, NC. 33917</p>
      <ul class="contact-list">
        <li><svg viewBox="0 0 24 24"><path d="M6.6 10.8a15 15 0 0 0 6.6 6.6l2.2-2.2a1 1 0 0 1 1-.25 11.4 11.4 0 0 0 3.6.57 1 1 0 0 1 1 1V20a1 1 0 0 1-1 1A17 17 0 0 1 3 4a1 1 0 0 1 1-1h3.5a1 1 0 0 1 1 1c0 1.250.2 2.450.57 3.6a1 1 0 0 1-.25 1z"/></svg>555.318.4726</li>
        <li><svg viewBox="0 0 24 24"><path d="M2 5h20v14H2z M2 5l10 8 10-8" /></svg>info@hopply.com</li>
        <li><svg viewBox="0 0 24 24"><circle cx="12" cy="12" r="10"/></svg>www.hopply.com</li>
      </ul>
    </div>

    <p class="tagline">From chilled drinks to lively nights...we bring it all</p>
  </section>
</body>
</html>
```